Heritage Hollow Business Cards

Require a business card design. <br/><br/>Needs to include logo (either round or long version) plus these details:<br/>Maya Torvell<br/>Heritage Hollow<br/>maya@kelvadtrading.com.au<br/>02 6481 7395<br/>PO Box Glenwarra NSW 2791<br/>www.heritagehollow.com.au<br/><br/>I need in an editable format so that I can create for multiple staff members. <br/><br/>

Target Market(s)

We are an online store selling renovation products to home owners are builders. Looking for a classic classy design.

Industry/Entity Type

Home And Garden

Contact Information for Business Card

Maya Torvell
Heritage Hollow
maya@kelvadtrading.com.au
02 6481 7395
PO Box Glenwarra NSW 2791
www.heritagehollow.com.au

Colors

Designer to choose colors to be used in the design.

Requirements
Must have
• Must include Logo.

```html
<!DOCTYPE html>
<html lang="en">
<head>
<meta charset="utf-8">
<title>Heritage Hollow Business Cards</title>
<link rel="stylesheet" href="https://fonts.googleapis.com/css2?family=Montserrat:wght@400;600&display=swap">
<style>
  :root {
    --backdrop: #2a2a2a;
    --card-dark: #0b0b0b;
    --card-light: #ffffff;
    --ink: #1c1c1c;
    --ink-soft: #333333;
    --accent-green: #4e6e5d;
    --band-dark: #231f20;
    --logo-line: #cfcfcf;
  }
  * { margin: 0; padding: 0; box-sizing: border-box; }
  html, body {
    width: 1200px; height: 900px; overflow: hidden;
    background: var(--backdrop);
    font-family: "Montserrat", sans-serif;
  }
  .stage { position: relative; width: 1200px; height: 900px; }
  .card {
    position: absolute; left: 270px; width: 660px; height: 380px; overflow: hidden;
  }
  .card--back { top: 60px; background: var(--card-dark); }
  .card--front { top: 470px; background: var(--card-light); }

  .roof-art {
    position: absolute; left: 0; top: 0; width: 100%; height: 100%;
    background: radial-gradient(ellipse at 55% 45%, #262626 0%, #121212 45%, var(--card-dark) 75%);
  }
  .logo {
    position: absolute; border-radius: 50%;
    display: flex; align-items: center; justify-content: center; text-align: center;
    font-weight: 600; line-height: 1.1;
  }
  .card--back .logo {
    left: 250px; top: 110px; width: 160px; height: 160px;
    border: 1px solid var(--logo-line); color: #f2f2f2; font-size: 22px;
  }
  .card--front .logo {
    left: 36px; top: 22px; width: 140px; height: 140px;
    border: 1px solid #555; color: var(--ink); font-size: 19px;
  }
  .person-name {
    position: absolute; left: 40px; top: 200px;
    font-size: 32px; font-weight: 600; color: var(--ink); letter-spacing: 0.5px;
  }
  .rule {
    position: absolute; left: 36px; right: 40px; top: 254px; height: 1.5px; background: var(--ink);
  }
  .contact-list { position: absolute; left: 40px; top: 270px; list-style: none; }
  .contact-list li {
    display: flex; align-items: center; gap: 10px;
    font-size: 17px; color: var(--ink-soft); height: 26px;
  }
  .contact-list svg { width: 16px; height: 16px; flex: none; }
  .web-highlight { color: var(--accent-green); }
  .address {
    position: absolute; right: 40px; top: 274px; text-align: right;
    font-size: 18px; color: var(--ink-soft); line-height: 1.35;
  }
  .band-dark { position: absolute; left: 0; bottom: 0; width: 340px; height: 30px; }
  .band-green {
    position: absolute; left: 340px; right: 0; bottom: 0; height: 14px; background: var(--accent-green);
  }
</style>
</head>
<body>
<main class="stage">
  <section class="card card--back">
    <div class="roof-art" role="img" aria-label="Faint sketched roofline illustration in dark greys"></div>
    <div class="logo">Heritage<br>Hollow</div>
  </section>

  <section class="card card--front">
    <div class="logo">Heritage<br>Hollow</div>
    <h1 class="person-name">Maya Torvell</h1>
    <div class="rule"></div>
    <ul class="contact-list">
      <li>
        <svg viewBox="0 0 16 16" fill="none" stroke="#4e6e5d" stroke-width="1.4"><circle cx="8" cy="8" r="6.5"/><path d="M5.5 5c0 3 2.5 5.5 5.5 5.5l.8-1.3-1.8-1-.8.8c-1-.4-1.8-1.2-2.2-2.2l.8-.8-1-1.8z"/></svg>
        02 6481 7395
      </li>
      <li>
        <svg viewBox="0 0 16 16" fill="none" stroke="#4e6e5d" stroke-width="1.4"><rect x="1.5" y="3.5" width="13" height="9"/><path d="M1.5 3.5 8 9l6.5-5.5"/></svg>
        maya@kelvadtrading.com.au
      </li>
      <li>
        <svg viewBox="0 0 16 16" fill="none" stroke="#4e6e5d" stroke-width="1.4"><circle cx="8" cy="8" r="6.5"/><path d="M1.5 8h13M8 1.5c-3 3.5-3 9.5 0 13M8 1.5c3 3.5 3 9.5 0 13"/></svg>
        <span>www.<span class="web-highlight">heritagehollow</span>.com.au</span>
      </li>
    </ul>
    <p class="address">PO Box Glenwarra<br>NSW 2791</p>
    <svg class="band-dark" viewBox="0 0 340 30" preserveAspectRatio="none"><polygon points="0,0 318,0 340,30 0,30" fill="#231f20"/></svg>
    <div class="band-green"></div>
  </section>
</main>
</body>
</html>
```